Amber Reed Consulting Business Card

Hi Morwen. Thank you for your work on my coaching business card. I have another business which needs a new card. It is my counselling business. The best way to find out how to approach this project will be to go to my other website. www.amberreedconsulting.example.au and you will be able to see the colours scheme that I will require. White, Green and blue.

The tag line is Amber Reed Consulting So A calmer mind for a brighter day. The clients are varied but mostly middle class Australian. The card is to show on it the same details as my other business card but with a different phone number. The tag lines are obviously different. The phone number is 5863 1427 The addresses are all the same.

Again simple, professional sophisticated is best.

Industry/Entity Type

Business

```html
<!DOCTYPE html>
<html lang="en">
<head>
<meta charset="utf-8">
<title>Amber Reed Consulting Business Card</title>
<link href="https://fonts.googleapis.com/css2?family=Marcellus&family=Lato:wght@300;400&display=swap" rel="stylesheet">
<style>
  :root {
    --backdrop: #e9e6e1;
    --blue-light: #5f86cf;
    --blue-deep: #1b4696;
    --green-light: #cde76a;
    --green-deep: #8cc43c;
    --lime-rule: #a6d63a;
    --white: #ffffff;
    --white-soft: rgba(255,255,255,0.9);
  }
  * { margin: 0; padding: 0; box-sizing: border-box; }
  html, body {
    width: 1200px; height: 803px; overflow: hidden;
    background: var(--backdrop);
  }
  .canvas {
    position: relative; width: 1200px; height: 803px;
  }
  .card {
    position: absolute; top: 242px;
    width: 520px; height: 318px;
    border-radius: 3px;
    box-shadow: 0 10px 28px rgba(0,0,0,0.18);
    color: var(--white);
    overflow: hidden;
  }
  .card--front {
    left: 50px;
    background: linear-gradient(135deg, var(--blue-light) 0%, var(--blue-deep) 70%);
  }
  .card--back {
    left: 630px;
    background: linear-gradient(135deg, var(--green-light) 0%, var(--green-deep) 80%);
  }

  /* Front */
  .front-brand {
    position: absolute; left: 34px; top: 150px;
    font-family: "Marcellus", serif; font-size: 40px; letter-spacing: 1px;
    color: var(--white-soft);
  }
  .front-rule {
    position: absolute; left: 26px; right: 24px; top: 203px;
    height: 2px; background: var(--lime-rule);
  }
  .front-tagline {
    position: absolute; left: 36px; top: 213px;
    font-family: "Lato", sans-serif; font-weight: 300;
    font-size: 17px; letter-spacing: 2px; text-transform: uppercase;
  }
  .front-services {
    position: absolute; left: 36px; top: 240px;
    font-family: "Lato", sans-serif; font-weight: 400;
    font-size: 12.5px; letter-spacing: 1.6px; line-height: 18px; text-transform: uppercase;
  }

  /* Back */
  .back-person {
    position: absolute; left: 26px; top: 26px;
    font-family: "Lato", sans-serif; font-weight: 300;
    font-size: 19px; letter-spacing: 1.5px; text-transform: uppercase;
  }
  .back-person .role {
    font-size: 10.5px; letter-spacing: 0.3px; text-transform: none; font-weight: 400;
  }
  .back-brand {
    position: absolute; left: 24px; top: 58px;
    font-family: "Marcellus", serif; font-size: 38px; letter-spacing: 1px;
    color: var(--white-soft);
  }
  .back-rule {
    position: absolute; left: 22px; right: 22px; top: 108px;
    height: 1.5px; background: rgba(255,255,255,0.85);
  }
  .back-tagline {
    position: absolute; left: 26px; top: 117px;
    font-family: "Lato", sans-serif; font-weight: 300;
    font-size: 16px; letter-spacing: 2px; text-transform: uppercase;
  }
  .contact {
    position: absolute; left: 26px; top: 176px; right: 20px;
    font-family: "Lato", sans-serif; font-size: 11px; letter-spacing: 0.3px;
  }
  .contact-grid {
    display: grid; grid-template-columns: 150px 1fr; row-gap: 5px; margin-bottom: 14px;
  }
  .contact-item { display: flex; align-items: center; gap: 6px; }
  .contact-item svg { width: 11px; height: 11px; flex: none; }
  .offices { list-style: none; line-height: 17px; }
</style>
</head>
<body>
<main class="canvas">

  <section class="card card--front" aria-label="Card front">
    <div class="front-brand">Amber Reed Consulting</div>
    <div class="front-rule"></div>
    <div class="front-tagline">A calmer mind for a brighter day</div>
    <div class="front-services">Advanced counselling • Coaching • Hypnotherapy<br>and psychotherapy</div>
  </section>

  <section class="card card--back" aria-label="Card back">
    <div class="back-person">Dana Whitfield <span class="role">Clinical Psychotherapist and Executive Coach</span></div>
    <div class="back-brand">Amber Reed Consulting</div>
    <div class="back-rule"></div>
    <div class="back-tagline">A calmer mind for a brighter day</div>

    <div class="contact">
      <div class="contact-grid">
        <div class="contact-item">
          <svg viewBox="0 0 12 12" aria-hidden="true"><path fill="#fff" d="M2.5 1l2 2.2-1 1.2c.6 1.4 1.7 2.5 3.1 3.1l1.2-1L10 8.5 9 10.5C5 10.4 1.6 7 1.5 3z"/></svg>
          <span>+612 5863 1427</span>
        </div>
        <div class="contact-item">
          <svg viewBox="0 0 12 12" aria-hidden="true"><rect x="1" y="2.5" width="10" height="7" fill="none" stroke="#fff" stroke-width="1.2"/><path d="M1 2.8l5 3.6 5-3.6" fill="none" stroke="#fff" stroke-width="1.2"/></svg>
          <span>dana@danawhitfield.example.au</span>
        </div>
        <div class="contact-item">
          <svg viewBox="0 0 12 12" aria-hidden="true"><rect x="1.5" y="4" width="9" height="6" fill="#fff"/><rect x="3.5" y="1.5" width="5" height="3" fill="none" stroke="#fff"/></svg>
          <span>+612 5863 1429</span>
        </div>
        <div class="contact-item">
          <svg viewBox="0 0 12 12" aria-hidden="true"><circle cx="6" cy="6" r="4.8" fill="none" stroke="#fff" stroke-width="1.1"/><path d="M1.2 6h9.6M6 1.2c-2.4 2.6-2.4 7 0 9.6M6 1.2c2.4 2.6 2.4 7 0 9.6" fill="none" stroke="#fff" stroke-width="0.9"/></svg>
          <span>www.amberreedconsulting.example.au</span>
        </div>
      </div>
      <ul class="offices">
        <li>Ashfield Office: 48 Harbour Lane Ashfield NSW 2131</li>
        <li>Northbank Office: Suite 210 / 17 Ridge Street Northbank NSW 2065</li>
        <li>Carrow Street Office: Suite 512 / 88 Carrow Street Sydney CBD NSW 2000</li>
      </ul>
    </div>
  </section>

</main>
</body>
</html>
```